Web page for a garment manufacturing company

We are clothing manufacturer based in Romania.
With our recent expansion, we have significantly increased our internal capacity, allowing us to take on new partnerships and deliver high-quality production services.
Our expertise includes producing classic coats, blazers, trousers, skirts, dresses, and blouses, though we are flexible and open to working with various other textile products.

Target Market(s)

High-end market and luxury

Industry/Entity Type

Garments Manufacturer

Coding

Coded - Design and coding required

Number of Pages Required

1 page

Colors

Designer to choose only greyscale colors for use in the design.

Requirements
Must have
• Velmora logo from our presentation
Nice to have
• https://www.lorvani.pt/
Should not have
• prices, wedding dresses, collections

```html
<!DOCTYPE html>
<html lang="en">
<head>
<meta charset="UTF-8">
<title>Velmora – Garment Manufacturing</title>
<link rel="stylesheet" href="https://fonts.googleapis.com/css2?family=Jost:wght@300;400;500;600;700&family=Open+Sans:wght@400;600&display=swap">
<style>
:root{
  --accent:#4a4a4a;
  --accent-band:#5a5a5a;
  --ink:#1f1f1f;
  --text:#444;
  --dark:#2a2a2a;
  --light:#f4f4f4;
  --white:#fff;
  --photo-a:#8e8e8e;
  --photo-b:#bcbcbc;
}
*{margin:0;padding:0;box-sizing:border-box}
html,body{width:1200px;height:4204px;overflow:hidden}
body{font-family:"Open Sans",sans-serif;color:var(--text);background:var(--white);position:relative}
h1,h2,h3,.brand,.nav,.btn{font-family:"Jost",sans-serif}
.photo{background:linear-gradient(135deg,var(--photo-b),var(--photo-a));position:absolute}

/* header */
.site-header{position:absolute;top:0;left:0;width:1200px;height:80px;display:flex;align-items:center;padding:0 112px;justify-content:space-between;background:var(--white)}
.brand{font-size:38px;font-weight:300;color:var(--ink);letter-spacing:1px}
.nav{display:flex;align-items:center;gap:30px;font-size:17px;color:var(--ink)}
.nav .active{color:var(--accent);font-weight:500;border-bottom:2px solid var(--accent);padding-bottom:2px}
.nav .cta{background:var(--dark);color:var(--white);padding:10px 22px;font-weight:600}

/* hero */
.hero{position:absolute;top:80px;left:0;width:1200px;height:580px;background:linear-gradient(160deg,#d2d2d2 0%,#8c8c8c 45%,#373737 100%)}
.hero-text{position:absolute;top:300px;width:100%;text-align:center;color:var(--white)}
.hero-text h1{font-size:64px;font-weight:600;letter-spacing:1px}
.hero-text p{font-size:17px;margin-top:10px;line-height:1.5}

/* sections */
.section-title{position:absolute;left:0;width:1200px;text-align:center;font-size:40px;font-weight:600;color:var(--ink)}
.lead{position:absolute;left:180px;width:840px;text-align:center;font-size:15px;line-height:1.75}
.btn{position:absolute;background:var(--accent);color:var(--white);font-size:16px;font-weight:500;padding:12px 32px;white-space:nowrap}
.btn.center{left:50%;transform:translateX(-50%)}

/* mission */
.mission{position:absolute;top:1628px;left:0;width:1200px;height:464px;background:linear-gradient(180deg,#dadada 0%,#a4a4a4 55%,#6c6c6c 100%)}
.mission-card{position:absolute;left:604px;top:72px;width:556px;height:340px;background:rgba(255,255,255,.95);border:2px solid #ddd;outline:8px solid rgba(255,255,255,.5);text-align:center;padding:28px 40px}
.mission-card h2{font-size:32px;color:var(--accent);font-weight:600;letter-spacing:1px}
.mission-card p{font-size:15px;line-height:1.85;margin-top:14px}
.mission-card .btn{position:static;display:inline-block;margin-top:16px}

/* cards */
.caption{position:absolute;bottom:14px;left:0;width:100%;text-align:center;color:var(--white);font-family:"Jost",sans-serif;font-weight:600;font-size:17px;line-height:1.3}
.card-big .caption{font-size:24px;bottom:18px}

/* newsletter */
.newsletter{position:absolute;top:3500px;left:0;width:1200px;height:260px;background:var(--accent-band);text-align:center;color:var(--white)}
.news-icon{position:absolute;left:576px;top:10px;width:48px;height:48px;border-radius:50%;background:var(--white);display:flex;align-items:center;justify-content:center}
.newsletter h2{position:absolute;top:90px;width:100%;font-size:36px;font-weight:600}
.news-form{position:absolute;top:170px;left:168px;width:864px;height:48px;background:var(--white);display:flex;justify-content:space-between;align-items:center;padding:0 6px 0 24px}
.news-form span{color:#555;font-size:15px}
.news-form b{background:var(--dark);color:var(--white);font-family:"Jost",sans-serif;font-weight:600;padding:9px 30px;font-size:16px}

/* footer */
.site-footer{position:absolute;top:3760px;left:0;width:1200px;height:444px;background:var(--dark);color:var(--white)}
.site-footer .brand{position:absolute;left:112px;top:120px;color:var(--white);font-size:52px}
.foot-col{position:absolute;top:112px}
.foot-col h3{font-size:26px;font-weight:500;margin-bottom:18px}
.foot-col li{list-style:none;font-size:15px;margin-bottom:12px;display:flex;align-items:center;gap:12px}
.foot-col li::before{content:"";width:7px;height:7px;border-radius:50%;background:var(--white)}
.foot-col.contact li{margin-bottom:22px}
.foot-col.contact li::before{display:none}
.ico{width:32px;height:32px;border-radius:50%;background:var(--white);display:flex;align-items:center;justify-content:center;flex:none}
.foot-rule{position:absolute;left:112px;top:380px;width:1088px;height:1px;background:#666}
.copyright{position:absolute;top:402px;width:100%;text-align:center;font-size:14px}
</style>
</head>
<body>

<header class="site-header">
  <div class="brand">Velmora</div>
  <nav class="nav">
    <span class="active">Home</span><span>About Us</span><span>Services</span><span>Merchandisers</span><span class="cta">Contact Us</span>
  </nav>
</header>

<section class="hero" role="img" aria-label="Velmora factory building exterior with company name on the facade">
  <div class="hero-text">
    <h1>Welcome to Velmora</h1>
    <p>Established in 2005 as a Joint Venture between a local manufacturer and<br>a foreign investor</p>
  </div>
</section>

<h2 class="section-title" style="top:736px">About Velmora</h2>
<p class="lead" style="top:812px">VELMORA is a manufacturing company for Ready-to-wear, situated in Varenta, a city with a rich tradition in the clothing industry. The top management is international, and we are proud to have a diverse and dynamic group of professionals from different countries working together. With our optimistic team spirit and passion for high-quality productions, we are ready to take on new challenges and delight our clients with very good results in different specialized workshops making woven garments, knitting, leather goods, bags, leather accessories, bed linen, being always open to new projects and challenges.</p>

<div class="photo" style="left:112px;top:1124px;width:188px;height:196px" role="img" aria-label="Team members reviewing a garment"></div>
<div class="photo" style="left:308px;top:1012px;width:340px;height:208px" role="img" aria-label="Pattern design workstation with computer screens"></div>
<div class="photo" style="left:660px;top:1048px;width:160px;height:160px" role="img" aria-label="Sewing workshop"></div>
<div class="photo" style="left:312px;top:1228px;width:156px;height:152px" role="img" aria-label="Fabric cutting area"></div>
<div class="photo" style="left:480px;top:1212px;width:348px;height:248px" role="img" aria-label="Automated cutting table in the production hall"></div>
<div class="photo" style="left:840px;top:1160px;width:220px;height:240px" role="img" aria-label="Worker operating an industrial machine"></div>
<span class="btn center" style="top:1496px">About Us</span>

<section class="mission" role="img" aria-label="Velmora headquarters building with parked cars">
  <div class="mission-card">
    <h2>MISSION</h2>
    <p>To provide exceptional quality products and services, to meet our customers' expectations while being environmentally and socially responsible in every aspect of our business. Additionally, we recognize and value the importance of our workers, ensuring their well-being and fostering a positive and inclusive work environment.</p>
    <span class="btn">About Us</span>
  </div>
</section>

<h2 class="section-title" style="top:2226px">Extra Benefits for people</h2>
<p class="lead" style="top:2300px">High-quality products and services; Continuously improve our products and services, focusing on exceptional quality, durability, and customer satisfaction.</p>

<div class="photo" style="left:112px;top:2500px;width:168px;height:260px" role="img" aria-label="Meal vouchers for employees"><span class="caption">Food tickets</span></div>
<div class="photo" style="left:296px;top:2404px;width:608px;height:384px" role="img" aria-label="Employees working in the office"><span class="caption">Paid transportation for employees, in very good conditions</span></div>
<div class="photo" style="left:916px;top:2408px;width:172px;height:252px" role="img" aria-label="Legal advisory office"><span class="caption">Lawyer employee's<br>legal services</span></div>
<span class="btn center" style="top:2792px">View More Benefits</span>

<h2 class="section-title" style="top:2934px">Velmora Community Activities</h2>
<div class="photo card-big" style="left:112px;top:3028px;width:308px;height:320px" role="img" aria-label="Group of children at summer camp"><span class="caption">Summer Camp</span></div>
<div class="photo card-big" style="left:444px;top:3028px;width:312px;height:320px" role="img" aria-label="Carved pumpkins for Halloween"><span class="caption">Halloween party</span></div>
<div class="photo card-big" style="left:776px;top:3028px;width:312px;height:320px" role="img" aria-label="Decorated Christmas tree and drawings"><span class="caption">Christmas creativity</span></div>
<span class="btn center" style="top:3382px">View More</span>

<section class="newsletter">
  <div class="news-icon">
    <svg width="22" height="18" viewBox="0 0 22 18"><rect x="1" y="1" width="20" height="16" rx="2" fill="none" stroke="#5a5a5a" stroke-width="2"/><path d="M1 3l10 7 10-7" fill="none" stroke="#5a5a5a" stroke-width="2"/></svg>
  </div>
  <h2>Signup to join Our Newsletter</h2>
  <div class="news-form"><span>Email Address</span><b>Subscribe</b></div>
</section>

<footer class="site-footer">
  <div class="brand">Velmora</div>
  <div class="foot-col" style="left:368px">
    <h3>Quick Links</h3>
    <ul><li>Home</li><li>About Us</li><li>Services</li><li>Merchandisers</li><li>Contact Us</li></ul>
  </div>
  <div class="foot-col" style="left:580px">
    <h3>Quick Links</h3>
    <ul><li>Privacy Policy</li><li>Terms and Condition</li><li>Support Links</li><li>Terms of Use</li><li>Faq</li></ul>
  </div>
  <div class="foot-col contact" style="left:828px">
    <h3>Contact Us</h3>
    <ul>
      <li><span class="ico"><svg width="14" height="18" viewBox="0 0 14 18"><path d="M7 1a6 6 0 0 1 6 6c0 4-6 10-6 10S1 11 1 7a6 6 0 0 1 6-6z" fill="#2a2a2a"/><circle cx="7" cy="7" r="2" fill="#fff"/></svg></span>Company Name, Romania</li>
      <li><span class="ico"><svg width="16" height="12" viewBox="0 0 16 12"><rect width="16" height="12" rx="1" fill="#2a2a2a"/><path d="M1 1l7 5 7-5" fill="none" stroke="#fff" stroke-width="1.4"/></svg></span>info@companyname.ro</li>
      <li><span class="ico"><svg width="16" height="16" viewBox="0 0 16 16"><path d="M3 1l3 3-2 2c1 2 3 4 6 6l2-2 3 3-2 2C7 15 1 9 1 3z" fill="#2a2a2a"/></svg></span>+1000 0000 0000</li>
    </ul>
  </div>
  <div class="foot-rule"></div>
  <p class="copyright">Copyrights@2024 Velmora.All Rights Reserved</p>
</footer>

</body>
</html>
```